SkyvornQ Business Cards and Stationary Design

Need a design for our business cards and stationary. I want to carry on the theme of the logo. I want the business cards to have a design on the back. I would like the business cards and the stationary to carry the same theme, design scheme, and branding

Target Market(s)

Airlines and Maintenance Facilities

Industry/Entity Type

Aviation

Contact Information for Business Card

Name
Position Title
Address: 4827 Trellis Hollow Road, Fort Pierce, Florida, 34951
Office Number
Mobile Number
Email
Website

Font styles to use
Serif
Sans Serif

Colors

Designer to choose colors to be used in the design.

```html
<!DOCTYPE html>
<html lang="en">
<head>
<meta charset="utf-8">
<title>SkyvornQ Business Card</title>
<link href="https://fonts.googleapis.com/css2?family=Open+Sans:wght@400&family=Source+Sans+3:wght@400;700&display=swap" rel="stylesheet">
<style>
  :root {
    --navy: #13294f;
    --ocean: #0a5591;
    --sky: #27a2dc;
    --paper: #ffffff;
    --stage-light: #77787b;
    --stage-dark: #2c2c2c;
  }
  html, body {
    margin: 0;
    width: 1200px;
    height: 809px;
    overflow: hidden;
  }
  body {
    position: relative;
    background: linear-gradient(135deg, var(--stage-light) 0%, #5f6063 55%, var(--stage-dark) 100%);
    font-family: "Open Sans", sans-serif;
  }
  .card {
    position: absolute;
    background: var(--paper);
    box-shadow: 0 0 0 1px #2a2a2a;
  }

  /* Front card */
  .card-front {
    left: 56px; top: 59px; width: 379px; height: 666px;
  }
  .brand-mark {
    position: absolute;
    left: 126px; top: 22px;
    width: 96px; height: 96px;
    border-radius: 50%;
    border: 8px solid var(--ocean);
    box-sizing: border-box;
  }
  .brand-name {
    position: absolute;
    left: 0; width: 100%;
    text-align: center;
    font-family: "Source Sans 3", sans-serif;
    font-weight: 700;
    color: var(--navy);
    letter-spacing: 7px;
    text-transform: uppercase;
  }
  .card-front .brand-name {
    top: 131px;
    font-size: 38px;
    line-height: 46px;
  }
  .person {
    position: absolute;
    left: 0; top: 199px; width: 100%; height: 68px;
    background: var(--navy);
    color: var(--paper);
    font-family: "Source Sans 3", sans-serif;
    box-sizing: border-box;
    padding: 12px 0 0 28px;
  }
  .person-name {
    font-size: 23px; font-weight: 700; line-height: 26px; text-transform: uppercase;
  }
  .person-title {
    font-size: 17px; font-weight: 400; line-height: 22px; margin-top: 2px; text-transform: uppercase;
  }
  .contact {
    position: absolute;
    left: 0; width: 100%; height: 68px;
    color: var(--paper);
    display: flex; align-items: center;
  }
  .contact.light { background: var(--sky); }
  .contact.mid { background: var(--ocean); }
  .contact.dark { background: var(--navy); }
  .contact-icon {
    position: absolute;
    left: 12px; top: 9px;
    width: 50px; height: 50px;
  }
  .contact-text {
    position: absolute;
    left: 76px;
    font-size: 17.5px;
    line-height: 24px;
  }
  .row-office { top: 276px; }
  .row-mobile { top: 353px; }
  .row-email { top: 429px; }
  .row-web { top: 506px; }
  .row-address { top: 583px; }
  .row-address .contact-text { font-size: 16px; line-height: 22px; width: 290px; }

  /* Back card */
  .card-back {
    left: 474px; top: 236px; width: 666px; height: 382px;
  }
  .brand-ring {
    position: absolute;
    left: 45px; top: 48px;
    width: 290px; height: 290px;
    border-radius: 50%;
    border: 17px solid var(--ocean);
    box-sizing: border-box;
  }
  .card-back .brand-name {
    left: 359px; width: 292px;
    top: 150px;
    font-size: 38px;
    line-height: 46px;
  }
  .back-web {
    position: absolute;
    left: 359px; width: 292px; top: 201px;
    text-align: center;
    font-size: 15px;
    letter-spacing: 4px;
    color: #333a45;
  }
</style>
</head>
<body>

<section class="card card-front">
  <div class="brand-mark"></div>
  <div class="brand-name">SkyvornQ</div>

  <div class="person">
    <div class="person-name">Dalen Whitcombe</div>
    <div class="person-title">Chief Executive Officer</div>
  </div>

  <div class="contact light row-office">
    <svg class="contact-icon" viewBox="0 0 50 50" fill="none" stroke="#fff" stroke-width="2.5">
      <circle cx="25" cy="25" r="22.5"/>
      <path d="M20 14c-3 2-4 6-3 10 2 6 6 11 11 13 3 1 5 0 6-2l-4-5-3 2c-3-2-5-5-6-8l3-2-4-8z" stroke-width="2" stroke-linejoin="round"/>
    </svg>
    <span class="contact-text">012-345-6789</span>
  </div>

  <div class="contact mid row-mobile">
    <svg class="contact-icon" viewBox="0 0 50 50" fill="none" stroke="#fff" stroke-width="2.5">
      <circle cx="25" cy="25" r="22.5"/>
      <rect x="18" y="12" width="14" height="26" rx="2.5" stroke-width="2"/>
      <line x1="19" y1="16" x2="31" y2="16" stroke-width="1.5"/>
      <line x1="19" y1="33" x2="31" y2="33" stroke-width="1.5"/>
      <circle cx="25" cy="35.5" r="0.8" fill="#fff" stroke="none"/>
    </svg>
    <span class="contact-text">012-345-6789</span>
  </div>

  <div class="contact dark row-email">
    <svg class="contact-icon" viewBox="0 0 50 50" fill="none" stroke="#fff" stroke-width="2.5">
      <circle cx="25" cy="25" r="22.5"/>
      <path d="M11 22 L25 13 L39 22 V35 H11 Z" fill="#fff" stroke="none"/>
      <path d="M11 22 L25 31 L39 22 M11 35 L21 28 M39 35 L29 28" stroke="var(--navy)" stroke-width="1.5"/>
      <line x1="20" y1="20" x2="30" y2="20" stroke="var(--navy)" stroke-width="1.5"/>
      <line x1="20" y1="23" x2="30" y2="23" stroke="var(--navy)" stroke-width="1.5"/>
    </svg>
    <span class="contact-text">info@skyvornq.com</span>
  </div>

  <div class="contact light row-web">
    <svg class="contact-icon" viewBox="0 0 50 50" fill="none" stroke="#fff" stroke-width="2.5">
      <circle cx="25" cy="25" r="22.5"/>
      <g stroke-width="1.6">
        <circle cx="25" cy="25" r="13"/>
        <ellipse cx="25" cy="25" rx="6" ry="13"/>
        <line x1="12" y1="25" x2="38" y2="25"/>
        <path d="M14 18 H36 M14 32 H36"/>
        <line x1="25" y1="12" x2="25" y2="38"/>
      </g>
    </svg>
    <span class="contact-text">www.skyvornq.com</span>
  </div>

  <div class="contact mid row-address">
    <svg class="contact-icon" viewBox="0 0 50 50" fill="none" stroke="#fff" stroke-width="2.5">
      <circle cx="25" cy="25" r="22.5"/>
      <circle cx="25" cy="25" r="14" fill="#fff" stroke="none"/>
      <path d="M25 35 C20 29 19 26 19 23 a6 6 0 0 1 12 0 c0 3-1 6-6 12z" fill="var(--ocean)" stroke="none"/>
      <circle cx="25" cy="23" r="2.2" fill="#fff" stroke="none"/>
    </svg>
    <span class="contact-text">4827 Trellis Hollow Road, Fort Pierce, Florida, 34951</span>
  </div>
</section>

<section class="card card-back">
  <div class="brand-ring"></div>
  <div class="brand-name">SkyvornQ</div>
  <div class="back-web">www.skyvornq.com</div>
</section>

</body>
</html>
```